Bahamas Pharmacy needs Flyer to Promote "Blood Pressure Tracking Service"

We need a double sided flyer design 5.5" x 8.5" (redesign) to promote a "Blood Pressure Tracking Service". Persons that have a card will be able to track their blood pressure online through a secure online blood pressure tracker. Clients of Coral Tide Pharmacy will be to test themselves--so information is confidential. Test Regularly - their information is stored up to 30 readings. Share the printed results. Flyer must contain endorsement logos of Silver Reef Cardiac Association Flyer and Palm Crest Glucose Association. The final design should communicate responsible tracking of health of elders and parents look clean, crisp, elegant modern yet simplistic. Any imagery should be friendly to the mixed-race demographic of the Bahamas. Contain imagery on either side of "Chatterloop and Pipsqueak"

Target Market(s)

Families

Industry/Entity Type

Health

Font styles to use
Sans Serif

Colors
0255a3
9ccb3b
ffffff
ec2027

Requirements
Must have
• Images of Happy African-American or Mixed-Race Family, Similar Aesthetic to "Perks Circle" flyer
Nice to have
• Imagery of Nurse taking blood pressure monitor, please see example of imagery type to be used.
Should not have
• Too much text, Small Imagery,

```html
<!DOCTYPE html>
<html lang="en">
<head>
<meta charset="utf-8">
<title>Blood Pressure Tracking Service – Coral Tide Pharmacy</title>
<link rel="stylesheet" href="https://fonts.googleapis.com/css2?family=Roboto+Condensed:wght@400;700&family=Roboto:wght@400&display=swap">
<style>
  :root {
    --page-bg: #e6e8e4;
    --green-deep: #0f6a2c;
    --green-main: #1b8a3d;
    --green-light: #2fa04c;
    --green-footer: #17843a;
    --silver-light: #ffffff;
    --silver-mid: #d9dbdc;
    --silver-dark: #b9bcbe;
    --brand-red: #c8202b;
    --brand-green: #1d7a35;
    --text-white: #ffffff;
    --rule: rgba(255,255,255,0.18);
  }
  * { margin: 0; padding: 0; box-sizing: border-box; }
  html, body { width: 841px; height: 1200px; overflow: hidden; }
  body { background: var(--page-bg); position: relative; font-family: "Roboto Condensed", "Arial Narrow", sans-serif; }

  .flyer { position: absolute; left: 91px; top: 90px; width: 659px; height: 1018px; overflow: hidden; background: var(--green-main); box-shadow: 0 2px 8px rgba(0,0,0,0.25); }
  .flyer-art { position: absolute; inset: 0; }

  .service-title {
    position: absolute; left: 0; top: 405px; width: 659px; height: 50px;
    padding-left: 20px; line-height: 50px;
    color: var(--text-white); font-weight: 700; font-size: 28px; letter-spacing: 0.2px;
  }
  .service-points { position: absolute; left: 0; top: 470px; width: 659px; list-style: none; }
  .service-point {
    color: var(--text-white); font-size: 19px; line-height: 27px;
    padding: 6px 20px 6px 21px; border-bottom: 1px solid var(--rule);
  }
  .service-point:last-child { border-bottom: none; }

  .brand { position: absolute; left: 238px; top: 826px; display: flex; align-items: center; gap: 10px; }
  .brand-dot { width: 30px; height: 30px; border-radius: 50%; background: var(--brand-red); }
  .brand-name { color: var(--brand-red); font-size: 24px; font-weight: 400; letter-spacing: 0.4px; }
  .brand-tagline { position: absolute; left: 365px; top: 872px; color: var(--brand-green); font-size: 14px; }

  .contact { position: absolute; left: 0; top: 926px; width: 659px; text-align: center; color: var(--text-white); font-family: "Roboto", Arial, sans-serif; font-size: 16.5px; line-height: 26px; }
  .contact-numbers { display: flex; justify-content: center; align-items: center; gap: 10px; margin-top: 4px; }
  .contact-numbers svg { width: 16px; height: 16px; }
  .contact-gap { width: 12px; }
</style>
</head>
<body>
<main class="flyer">
  <svg class="flyer-art" width="659" height="1018" viewBox="0 0 659 1018" aria-hidden="false">
    <defs>
      <linearGradient id="photoTones" x1="0" y1="0" x2="1" y2="1">
        <stop offset="0" stop-color="#9bb36a"/>
        <stop offset="0.35" stop-color="#c9705f"/>
        <stop offset="0.6" stop-color="#6f7f3a"/>
        <stop offset="1" stop-color="#3f5a22"/>
      </linearGradient>
      <linearGradient id="panelGreen" x1="0" y1="0" x2="0" y2="1">
        <stop offset="0" stop-color="#238f40"/>
        <stop offset="1" stop-color="#137734"/>
      </linearGradient>
      <linearGradient id="titleBand" x1="0" y1="0" x2="1" y2="0">
        <stop offset="0" stop-color="#0d5f26" stop-opacity="0.85"/>
        <stop offset="0.7" stop-color="#0d5f26" stop-opacity="0.35"/>
        <stop offset="1" stop-color="#0d5f26" stop-opacity="0"/>
      </linearGradient>
      <linearGradient id="silverSweep" x1="0" y1="0" x2="1" y2="0">
        <stop offset="0" stop-color="#c3c6c8"/>
        <stop offset="0.5" stop-color="#ffffff"/>
        <stop offset="1" stop-color="#cfd2d3"/>
      </linearGradient>
      <linearGradient id="silverPanel" x1="0" y1="0" x2="1" y2="1">
        <stop offset="0" stop-color="#bfc2c4"/>
        <stop offset="0.5" stop-color="#ffffff"/>
        <stop offset="1" stop-color="#d4d6d7"/>
      </linearGradient>
    </defs>

    <rect class="hero-photo" x="0" y="0" width="659" height="390" fill="url(#photoTones)" role="img" aria-label="Photo: smiling senior couple sitting together outdoors among green trees"/>

    <path class="panel" d="M0,372 C240,372 480,320 659,222 L659,1018 L0,1018 Z" fill="url(#panelGreen)"/>
    <path class="sweep" d="M0,354 C240,360 470,305 659,210 L659,226 C480,322 250,378 0,378 Z" fill="url(#silverSweep)"/>

    <rect class="title-band" x="0" y="405" width="659" height="50" fill="url(#titleBand)"/>

    <path class="lower-sweep-edge" d="M659,700 C430,700 210,760 0,905 L0,915 C220,775 440,712 659,712 Z" fill="#2fa04c"/>
    <path class="lower-silver" d="M659,712 C440,712 220,775 0,915 L659,915 Z" fill="url(#silverPanel)"/>

    <rect class="footer-band" x="0" y="915" width="659" height="103" fill="var(--green-footer)"/>
  </svg>

  <h1 class="service-title">Blood Pressure Tracking Service</h1>
  <ul class="service-points">
    <li class="service-point">View your results online through a secure online blood pressure tracker (see reverse for instructions)</li>
    <li class="service-point">Test yourself on the blood pressure kiosk - simple and easy</li>
    <li class="service-point">Test regularly-the card will store 30 readings and the ticket will print the average of your last 10 results and pulse rate.</li>
    <li class="service-point">Share the printed results with your pharmacist/doctor to help manage your health!</li>
  </ul>

  <div class="brand">
    <span class="brand-dot"></span>
    <span class="brand-name">Coral Tide Pharmacy</span>
  </div>
  <p class="brand-tagline">Healthier choices, Lower Prices</p>

  <address class="contact" style="font-style:normal">
    <div>14 Harbour View Drive, Seabreeze Plaza</div>
    <div>P.O.Box C 51870, Freeport, Grand Bahama, Bahamas</div>
    <div class="contact-numbers">
      <svg viewBox="0 0 16 16" aria-label="Phone"><circle cx="8" cy="8" r="7" fill="none" stroke="#fff" stroke-width="1.2"/><path d="M5.5 4.5 L7 6 L6.2 7 C6.8 8.2 7.8 9.2 9 9.8 L10 9 L11.5 10.5 L10.6 11.6 C8 11.2 4.8 8 4.4 5.4 Z" fill="#fff"/></svg>
      <span>(242) 555 0147 / 8</span>
      <span class="contact-gap"></span>
      <svg viewBox="0 0 16 16" aria-label="Fax"><rect x="4" y="3" width="8" height="4" fill="#fff"/><rect x="2" y="7" width="12" height="6" rx="1.5" fill="#fff"/><rect x="5" y="9" width="6" height="1.2" fill="var(--green-footer)"/></svg>
      <span>(242) 555 0149</span>
    </div>
  </address>
</main>
</body>
</html>
```